K & R Acre Works. Business card design

We need a business card designed for a new business. We have a bulldozer and tractor service. We clear land and make wildlife food plots. We provide disking, bush hogging, and site prep services.
I have attached an image of a business card that I like and would like my business cards to look similar.

Target Market(s)

anyone needing bulldozer and/or tractor services

Industry/Entity Type

Business

Contact Information for Business Card

K & R Acre Works, Operated by 7-T-Ranch
Wade Colton
601-472-3358
wcr4817@fieldmail-example.com

Font styles to use
Sans Serif

Colors

Designer to choose colors to be used in the design.

Requirements
Must have
• image of tractor and bulldozer
• Land Clearing
• Wildlife food plots
• Bush Hogging
• Disking
• Site prep
Nice to have
• i have included a image of a business card that i like. I would like mine to be similar.

```html
<!DOCTYPE html>
<html lang="en">
<head>
<meta charset="utf-8">
<title>K &amp; R Acre Works — Business Card</title>
<link rel="stylesheet" href="https://fonts.googleapis.com/css2?family=Oswald:wght@400;500;600&family=Montserrat:wght@300&family=Open+Sans:wght@400&display=swap">
<style>
  :root {
    --page-bg: #d9d4cc;
    --card-black: #0b0b0c;
    --card-top: #1a1a1c;
    --accent-red: #e4463f;
    --text-white: #f4f4f4;
    --text-grey: #bdbdbd;
    --photo-field: #6f7d4c;
    --photo-sky: #8fa6b8;
    --photo-dirt: #a58c66;
    --photo-orange: #b8513a;
    --photo-yellow: #b9a23c;
  }
  * { margin: 0; padding: 0; box-sizing: border-box; }
  html, body { width: 1200px; height: 1023px; overflow: hidden; }
  body {
    background: var(--page-bg);
    display: flex; align-items: center; justify-content: center;
  }
  .business-card {
    position: relative;
    width: 1000px; height: 572px;
    background: linear-gradient(160deg, var(--card-top) 0%, var(--card-black) 55%);
    overflow: hidden;
  }
  .brand-block { position: absolute; left: 70px; top: 62px; }
  .company-name {
    font-family: "Oswald", sans-serif; font-weight: 600;
    font-size: 46px; letter-spacing: 0.5px; text-transform: uppercase;
    color: var(--accent-red); line-height: 1;
  }
  .operated-by {
    margin-top: 12px;
    font-family: "Montserrat", sans-serif; font-weight: 300;
    font-size: 20px; letter-spacing: 6px; text-transform: uppercase;
    color: var(--text-grey);
  }
  .service-list {
    margin-top: 34px;
    font-family: "Oswald", sans-serif; font-weight: 500;
    font-size: 22px; letter-spacing: 0.5px; text-transform: uppercase;
    color: var(--text-white); line-height: 1.4;
  }
  .contact-block { position: absolute; right: 60px; top: 58px; text-align: left; }
  .owner-name {
    font-family: "Oswald", sans-serif; font-weight: 600;
    font-size: 52px; letter-spacing: 1px; text-transform: uppercase;
    color: var(--accent-red); line-height: 1;
  }
  .contact-line {
    display: flex; align-items: center; gap: 12px;
    margin-top: 16px;
    font-family: "Open Sans", sans-serif; font-size: 21px;
    color: var(--text-white);
  }
  .contact-line:first-of-type { margin-top: 26px; }
  .contact-icon { width: 18px; height: 18px; flex: none; }
  .photo-band {
    position: absolute; left: 0; right: 0; bottom: 0; height: 206px;
    border-top: 5px solid var(--accent-red);
    display: grid; grid-template-columns: repeat(4, 1fr); gap: 4px;
    background: var(--card-black);
  }
  .photo-slot { width: 100%; height: 100%; }
  .photo-tractor { background: linear-gradient(180deg, var(--photo-field) 0%, var(--photo-orange) 60%, var(--photo-dirt) 100%); }
  .photo-dozer-yard { background: linear-gradient(180deg, var(--photo-sky) 0%, var(--photo-yellow) 55%, var(--photo-dirt) 100%); }
  .photo-dozer-push { background: linear-gradient(180deg, var(--photo-field) 0%, var(--photo-yellow) 50%, #5b5346 100%); }
  .photo-dozer-trail { background: linear-gradient(180deg, #4f6b3a 0%, var(--photo-yellow) 50%, var(--photo-dirt) 100%); }
</style>
</head>
<body>
  <article class="business-card">
    <header class="brand-block">
      <h1 class="company-name">K &amp; R Acre Works</h1>
      <p class="operated-by">Operated by 7-T-Ranch</p>
      <p class="service-list">Land Clearing - Wildlife Food Plots<br>Bush Hogging - Disking - Site Prep</p>
    </header>

    <section class="contact-block">
      <h2 class="owner-name">Wade Colton</h2>
      <p class="contact-line">
        <svg class="contact-icon" viewBox="0 0 24 24" aria-hidden="true"><path d="M6.6 10.8a15 15 0 0 0 6.6 6.6l2.2-2.2a1 1 0 0 1 1-.25 11.4 11.4 0 0 0 3.6.57 1 1 0 0 1 1 1V20a1 1 0 0 1-1 1A17 17 0 0 1 3 4a1 1 0 0 1 1-1h3.5a1 1 0 0 1 1 1c0 1.25.2 2.45.57 3.57a1 1 0 0 1-.25 1z" fill="var(--accent-red)"/></svg>
        601-472-3358
      </p>
      <p class="contact-line">
        <svg class="contact-icon" viewBox="0 0 24 24" aria-hidden="true"><rect x="2.5" y="5" width="19" height="14" fill="none" stroke="var(--accent-red)" stroke-width="2.4"/><path d="M3 6l9 7 9-7" fill="none" stroke="var(--accent-red)" stroke-width="2.4"/></svg>
        wcr4817@fieldmail-example.com
      </p>
    </section>

    <div class="photo-band">
      <div class="photo-slot photo-tractor" role="img" aria-label="Photo of an orange tractor with a bush hog in a field"></div>
      <div class="photo-slot photo-dozer-yard" role="img" aria-label="Photo of a yellow bulldozer pushing dirt near a building"></div>
      <div class="photo-slot photo-dozer-push" role="img" aria-label="Photo of a yellow bulldozer clearing brush and soil"></div>
      <div class="photo-slot photo-dozer-trail" role="img" aria-label="Photo of a yellow bulldozer on a cleared woodland trail"></div>
    </div>
  </article>
</body>
</html>
```